rvl works packaging for accessories

mobile phone case, screen guard and accessory packaging
We would need 3 types of packaging:
Phone cases, which has a clear window in the front
Screen guard which will need to have screen guard written on front
And our other accessories packaging will be like the others but with no window and something eye catching.
i have added our packaging we will be using for our products in the attachments except for our other accessories will find and add.
we need

Target Market(s)

18-65+ who will be purchasing mobile phone accessories

Colors
ec1f27
000000
9d9d9d
ffffff

Requirements
Must have
• our logo
• colours from our logo black red and grey/silver and white
• 2 year warranty
• adequate space barcode
Nice to have
• would like a nice generic description for all products in the packaging. please email me if this does not make sense. marnie@rvlworks.com.au
• Wording to include "Our products have been hand-selected to ensure you are receiving the best products for your needs. We guarantee that you will be happy with your choice."

```html
<!DOCTYPE html>
<html lang="en">
<head>
<meta charset="utf-8">
<title>Easy Installation – Screen Guard</title>
<link rel="stylesheet" href="https://fonts.googleapis.com/css2?family=Exo+2:wght@700&family=Hind:wght@400&family=Open+Sans:ital,wght@1,300;1,400&display=swap">
<style>
  :root {
    --bg: #0b0b0b;
    --red: #ec1f27;
    --ring: #7a1a1e;
    --white: #ffffff;
    --text: #dcdcdc;
    --line: #cfcfcf;
    --icon-fill: #1a1a1a;
  }
  * { margin: 0; padding: 0; box-sizing: border-box; }
  html, body { width: 1200px; height: 659px; overflow: hidden; background: var(--bg); }
  .panel { position: relative; width: 1200px; height: 659px; background: var(--bg); overflow: hidden; }
  .accent-arcs {
    position: absolute; left: 1020px; top: 80px; width: 180px; height: 460px;
    background: radial-gradient(ellipse 100% 55% at 100% 50%, rgba(122,26,30,0.55) 0%, rgba(122,26,30,0.8) 55%, rgba(122,26,30,0.35) 85%, rgba(122,26,30,0) 100%);
  }
  .heading {
    position: absolute; left: 88px; width: 400px; top: 37px; text-align: center;
    font-family: "Exo 2", sans-serif; font-weight: 700; font-size: 25px;
    color: var(--red); letter-spacing: 0.3px; line-height: 32px;
  }
  .subheading {
    position: absolute; left: 48px; width: 480px; top: 72px; text-align: center;
    font-family: "Hind", sans-serif; font-size: 18.5px; color: var(--white); line-height: 24px;
  }
  .steps { position: absolute; left: 78px; top: 112px; list-style: none; }
  .step { position: absolute; left: 0; display: flex; align-items: flex-start; }
  .step-icon {
    position: relative; width: 46px; height: 46px; border: 1px solid var(--line);
    border-radius: 3px; background: var(--icon-fill); flex: none;
  }
  .step-number {
    position: absolute; right: -4px; top: -4px; width: 13px; height: 13px;
    border: 1px solid var(--line); border-radius: 50%; background: var(--bg);
    font-family: "Hind", sans-serif; font-size: 8px; line-height: 12px;
    text-align: center; color: var(--white);
  }
  .step-text {
    margin-left: 16px; margin-top: 9px; width: 362px;
    font-family: "Open Sans", sans-serif; font-style: italic; font-weight: 300; font-size: 9px;
    letter-spacing: 0.35px; line-height: 13px; color: var(--text);
  }
</style>
</head>
<body>
<main class="panel">
  <div class="accent-arcs" role="img" aria-label="Decorative red concentric arcs"></div>

  <h1 class="heading">EASY INSTALLATION</h1>
  <p class="subheading">Follow the steps below to install step by step</p>

  <ol class="steps">
    <li class="step" style="top:0">
      <div class="step-icon" role="img" aria-label="Icon: glass protector and its carrier"><span class="step-number">1</span></div>
      <p class="step-text">The glass screen protector is composed of two parts: a glass screen protector and a glass screen protector carrier marked with 1</p>
    </li>
    <li class="step" style="top:60px">
      <div class="step-icon" role="img" aria-label="Icon: hand wiping the device screen"><span class="step-number">2</span></div>
      <p class="step-text">Clean the device screen with the supplied cloth.</p>
    </li>
    <li class="step" style="top:127px">
      <div class="step-icon" role="img" aria-label="Icon: applying the dust film"><span class="step-number">3</span></div>
      <p class="step-text">Stick the blue dust film on the device screen firmly, and then pull it off slowly from one corner to make sure that the screen is cleaned thoroughly</p>
    </li>
    <li class="step" style="top:191px">
      <div class="step-icon" role="img" aria-label="Icon: placing location labels"><span class="step-number">4</span></div>
      <p class="step-text">Stick the two location labels on the lower left corner and upper right corner respectively.</p>
    </li>
    <li class="step" style="top:256px">
      <div class="step-icon" role="img" aria-label="Icon: peeling off the carrier"><span class="step-number">5</span></div>
      <p class="step-text">Peel off the glass screen protector carrier.</p>
    </li>
    <li class="step" style="top:324px">
      <div class="step-icon" role="img" aria-label="Icon: aligning the protector sheet"><span class="step-number">6</span></div>
      <p class="step-text">Align the glass screen protector perfectly by using the two location labels,and then set the sheet down.</p>
    </li>
    <li class="step" style="top:389px">
      <div class="step-icon" role="img" aria-label="Icon: pressing the protector with a finger"><span class="step-number">7</span></div>
      <p class="step-text">Carefully press the glass screen protector with your fingers th make it fit the device screen perfectly.</p>
    </li>
  </ol>
</main>
</body>
</html>
```